New Business Card Design Project

I need a design for business cards, i am an electrical business called "Corvane Electrical and Communications" i need the cards to be double sided with the company logo on the back (attached) the front needs to say my company name, web site, email address, telephone number, and ABN number and electrical license number. I am open to different arrangements of the information but would like the background to be incorporating something electrical or something that looks smart. open to all additional ideas also.

The company colours are orange and grey see logo attached.

Business Name: Corvane Electrical and Communications
Website: corvaneelectricalandcomms.example.com.au
Email: brent@corvaneelectricalandcomms.example.com.au
Telephone(mobile): 0481209736
ABN: 71208349162
Lic No: 418273D

Target Market(s)

Business entities, Project Managers, Accounts, Clients

Industry/Entity Type

Electrician

Contact Information for Business Card

I need a design for business cards, i am an electrical business called "Corvane Electrical and Communications" i need the cards to be double sided with the company logo on the back (attached) the front needs to say my company name

Font styles to use
Serif
Sans Serif

Colors
f37122
5c5c5c

Requirements
Must have
• Must have the Logo on the back open to different ways of it being on the back but had in mind to keep it central but again open to other options
Nice to have
• A real modern cool background that is eye catching yet contemporary
Should not have
• No backgrounds of a light bulb or plug or anything like that

```html
<!DOCTYPE html>
<html lang="en">
<head>
<meta charset="utf-8">
<title>Corvane Electrical and Communications – Business Card</title>
<link rel="stylesheet" href="https://fonts.googleapis.com/css2?family=Open+Sans:wght@400;600&display=swap">
<style>
  :root {
    --orange: #f37122;
    --orange-light: #ffc75f;
    --orange-mid: #fdb23a;
    --grey: #5c5c5c;
    --ink: #1e1e1e;
    --paper: #ffffff;
    --backdrop: #ecebe8;
  }
  * { box-sizing: border-box; margin: 0; padding: 0; }
  html, body {
    width: 1200px; height: 900px; overflow: hidden;
    background: var(--backdrop);
    font-family: "Open Sans", Arial, sans-serif;
  }
  .sheet {
    position: relative; width: 1200px; height: 900px;
    display: flex; align-items: center; justify-content: center; gap: 40px;
  }
  .card {
    position: relative; width: 540px; height: 309px;
    border-radius: 3px; overflow: hidden;
    box-shadow: 0 6px 18px rgba(0,0,0,.14);
  }
  /* Back side */
  .card--back {
    background: radial-gradient(ellipse at 45% 70%, var(--orange-light) 0%, var(--orange-mid) 75%);
  }
  .card--back .wordmark {
    position: absolute; left: 0; right: 0; top: 168px;
    text-align: center; color: var(--paper); font-weight: 400;
  }
  .wordmark__name { display: block; font-size: 46px; letter-spacing: 6px; line-height: 1; }
  .wordmark__line { display: block; font-size: 11px; letter-spacing: 1.6px; margin-top: 6px; }
  /* Front side */
  .card--front { background: var(--paper); }
  .card--front .wordmark {
    position: absolute; left: 34px; top: 44px;
    color: var(--grey); font-weight: 600;
  }
  .card--front .wordmark__name { font-size: 36px; letter-spacing: 4px; }
  .card--front .wordmark__line { font-size: 8.5px; letter-spacing: 1.2px; margin-top: 5px; }
  .details {
    position: absolute; left: 232px; top: 120px;
    color: var(--ink); font-size: 11.5px; line-height: 1.35;
  }
  .details__name { color: var(--orange); font-weight: 600; font-size: 16px; }
  .details__role { font-size: 11px; margin-bottom: 10px; }
  .details__id { font-weight: 600; font-size: 13px; }
  .details__id span { color: var(--orange); }
  .contact { list-style: none; margin-top: 10px; }
  .contact li { display: flex; align-items: center; gap: 7px; margin-bottom: 4px; }
  .contact svg { width: 10px; height: 10px; flex: none; fill: var(--orange); }
</style>
</head>
<body>
<main class="sheet">
  <section class="card card--back" aria-label="Card back">
    <div class="wordmark">
      <span class="wordmark__name">CORVANE</span>
      <span class="wordmark__line">ELECTRICAL &amp; COMMUNICATIONS</span>
    </div>
  </section>

  <section class="card card--front" aria-label="Card front">
    <div class="wordmark">
      <span class="wordmark__name">CORVANE</span>
      <span class="wordmark__line">ELECTRICAL &amp; COMMUNICATIONS</span>
    </div>
    <div class="details">
      <p class="details__name">Brent Halloway</p>
      <p class="details__role">Director</p>
      <p class="details__id"><span>ABN:</span> 71208349162</p>
      <p class="details__id"><span>Lic No:</span> 418273D</p>
      <ul class="contact">
        <li><svg viewBox="0 0 10 10" aria-hidden="true"><path d="M2 0.5 L3.6 2.6 L2.8 3.6 C3.4 5 4.9 6.6 6.4 7.2 L7.4 6.4 L9.5 8 L8.4 9.5 C4.6 9.2 0.8 5.4 0.5 1.6 Z"/></svg>0481209736</li>
        <li><svg viewBox="0 0 10 10" aria-hidden="true"><path d="M0.5 2 H9.5 V8.5 H0.5 Z M0.5 2 L5 5.6 L9.5 2" stroke="#fff" stroke-width="0.8"/></svg>brent@corvaneelectricalandcomms.example.com.au</li>
        <li><svg viewBox="0 0 10 10" aria-hidden="true"><circle cx="5" cy="5" r="4.5"/><path d="M0.5 5 H9.5 M5 0.5 C2.6 3 2.6 7 5 9.5 M5 0.5 C7.4 3 7.4 7 5 9.5" stroke="#fff" stroke-width="0.7" fill="none"/></svg>corvaneelectricalandcomms.example.com.au</li>
      </ul>
    </div>
  </section>
</main>
</body>
</html>
```